Martin R Cole DDS (dentist) needs a business card/business logo design

I would like an eye-catchingly conservative or elegant graphic presentation of my business name with the elements: prevention, restoration, and cosmetics (these are the services I'd like to emphasize) .
The business card would have room for address lines, phone and fax, web address. No standard teeth or oral representations please. Should communicate professionalism. Whatever color scheme works.

Thank you

Target Market(s)

I just want a good looking business card

Industry/Entity Type

Conservative

Contact Information for Business Card

Adress: 4163 Brisdale Ave Lakewood CA 90648 Phone: 562 419 3086 FAX 562 419 5274 Web: Fernhilldental.com

Font styles to use
Sans Serif

Colors
0255a3

Requirements
Must have
• business name with the elements: prevention, restoration, and cosmetics (these are the services I'd like to emphasize)
• communicates professionalism
Nice to have
• eye catching but not flashy graphics
Should not have
• no pictures of teeth or dental instruments

```html
<!DOCTYPE html>
<html lang="en">
<head>
<meta charset="utf-8">
<title>Martin R Cole DDS – Business Card</title>
<link rel="stylesheet" href="https://fonts.googleapis.com/css2?family=Ubuntu:wght@400;500;700&display=swap">
<style>
  :root {
    --page: #e4e5e7;
    --slate: #8c9198;
    --teal: #007b89;
    --white: #ffffff;
    --name-grey: #7a8088;
  }
  * { margin: 0; padding: 0; box-sizing: border-box; }
  html, body {
    width: 1200px; height: 1000px; overflow: hidden;
    background: var(--page);
    font-family: "Ubuntu", sans-serif;
  }
  .card {
    position: absolute; left: 75px; top: 200px;
    width: 1050px; height: 600px;
    background: var(--slate);
    overflow: hidden;
    box-shadow: 0 6px 18px rgba(0,0,0,0.18);
  }
  .brand-name {
    position: absolute; left: 120px; top: 95px;
    color: var(--white); font-weight: 700; font-size: 46px;
    letter-spacing: 0.5px;
  }
  .services {
    position: absolute; left: 120px; top: 205px;
    color: var(--white); font-weight: 500; font-size: 27px;
  }
  .contact-band {
    position: absolute; left: 0; top: 262px;
    width: 100%; height: 268px;
    background: var(--teal);
  }
  .name-tab {
    position: absolute; right: 0; top: 262px;
    width: 440px; height: 128px;
    background: var(--white);
    border-radius: 34px 0 0 34px;
    padding: 26px 34px 0 0;
    text-align: right;
  }
  .name-tab .person { color: var(--name-grey); font-weight: 700; font-size: 34px; }
  .name-tab .role { color: var(--name-grey); font-size: 23px; margin-top: 4px; }
  .contact-list {
    position: absolute; left: 90px; top: 300px;
    list-style: none;
  }
  .contact-list li {
    display: flex; align-items: center; gap: 12px;
    height: 48px;
    color: var(--white); font-size: 26px; font-weight: 500;
  }
  .contact-list svg { width: 30px; height: 30px; flex: none; }
</style>
</head>
<body>
  <div class="card">
    <div class="brand-name">Martin R Cole DDS</div>
    <div class="services">Prevention, Restoration and Cosmetics</div>
    <div class="contact-band"></div>
    <div class="name-tab">
      <div class="person">Martin R Cole DDS</div>
      <div class="role">Dentist</div>
    </div>
    <ul class="contact-list">
      <li>
        <svg viewBox="0 0 30 30" aria-hidden="true"><path fill="#fff" d="M3 12c0-4 5-6 12-6s12 2 12 6v2h-6v-3H9v3H3z"/><rect x="6" y="15" width="18" height="10" rx="2" fill="#fff"/><circle cx="15" cy="20" r="3" fill="#007b89"/></svg>
        <span>: 562- 419- 3086</span>
      </li>
      <li>
        <svg viewBox="0 0 30 30" aria-hidden="true"><rect x="9" y="3" width="12" height="8" fill="#fff"/><rect x="3" y="11" width="24" height="11" rx="2" fill="#fff"/><rect x="9" y="18" width="12" height="9" fill="#fff" stroke="#007b89" stroke-width="1.5"/></svg>
        <span>: 562- 419- 5274</span>
      </li>
      <li>
        <svg viewBox="0 0 30 30" aria-hidden="true"><circle cx="15" cy="15" r="12" fill="#fff"/><text x="15" y="18" font-size="8" font-family="Ubuntu, sans-serif" font-weight="700" text-anchor="middle" fill="#007b89">www</text></svg>
        <span>: www.Fernhilldental.com</span>
      </li>
      <li>
        <svg viewBox="0 0 30 30" aria-hidden="true"><path d="M15 3a6 6 0 0 1 6 6c0 5-6 11-6 11s-6-6-6-11a6 6 0 0 1 6-6z" fill="none" stroke="#fff" stroke-width="2"/><circle cx="15" cy="9" r="2" fill="#fff"/><path d="M4 20h5M21 20h5l2 7H2l2-7" fill="none" stroke="#fff" stroke-width="2"/></svg>
        <span>: 4163 Brisdale Ave, Lakewood, CA 90648</span>
      </li>
    </ul>
  </div>
</body>
</html>
```